Tovella Fireworks needs a web design and logo

We need a web design and logo for a fireworks business in Sydney Australia, we do public display, weddings, tv, theatrical, clubs and any other organisation that wants to do something special.
Name is Marrowind Fireworks & Pyrotechnics

```html
<!DOCTYPE html>
<html lang="en">
<head>
<meta charset="utf-8">
<title>Marrowind Fireworks &amp; Pyrotechnics</title>
<link href="https://fonts.googleapis.com/css2?family=Roboto:wght@300;400;500&display=swap" rel="stylesheet">
<style>
  :root {
    --ink: #000000;
    --paper: #ffffff;
    --muted: #6b6b6b;
    --night: #0d1f1a;
    --sky-green: #2f4a3a;
    --glow-gold: #d9a86a;
    --glow-blue: #4f8fe0;
    --stage: #1a1e2e;
    --field: #f2f2f2;
  }
  * { box-sizing: border-box; margin: 0; padding: 0; }
  html, body { width: 1200px; height: 1000px; overflow: hidden; background: var(--paper); }
  body { font-family: "Roboto", "Helvetica Neue", Arial, sans-serif; color: var(--ink); position: relative; }
  .page { position: absolute; left: 282px; top: 0; width: 627px; height: 1000px; }
  .abs { position: absolute; }
  .center { text-align: center; }

  .site-header { left: 0; top: 0; width: 627px; height: 49px; background: var(--ink); }
  .menu-icon { left: 5px; top: 21px; }
  .brand { left: 37px; top: 16px; color: var(--paper); font-size: 18px; font-weight: 300; white-space: nowrap; }

  .hero { left: 0; top: 49px; width: 627px; height: 299px;
    background:
      radial-gradient(circle at 89% 22%, rgba(120,170,255,.9) 0, rgba(79,143,224,.5) 8%, transparent 18%),
      radial-gradient(circle at 58% 42%, rgba(235,180,120,.75) 0, transparent 30%),
      radial-gradient(circle at 12% 36%, rgba(230,180,130,.6) 0, transparent 14%),
      radial-gradient(ellipse at 55% 95%, rgba(230,220,210,.55) 0, transparent 35%),
      linear-gradient(180deg, var(--night) 0%, var(--sky-green) 55%, #1b2622 100%);
  }
  .hero-title { left: 0; width: 640px; top: 61px; color: var(--paper); font-size: 26px; font-weight: 300; }
  .hero-sub { left: 220px; width: 200px; top: 94px; color: #e8e8e8; font-size: 9px; line-height: 15px; }

  .section-title { font-size: 22px; font-weight: 300; width: 627px; left: 0; }
  .services-title { top: 353px; }
  .service-photo { top: 395px; height: 116px; }
  .photo-craft { left: 35px; width: 154px; background: linear-gradient(135deg, #2a2a22, #8c8459 55%, #3a3a2c); }
  .photo-stage { left: 215px; width: 197px; background: radial-gradient(ellipse at 50% 40%, #c9ced8 0, #55607a 30%, var(--stage) 75%); }
  .photo-burst { left: 438px; width: 154px; background: radial-gradient(circle at 35% 45%, var(--glow-gold) 0, #5a3f20 25%, var(--ink) 55%); }
  .service-caption { top: 523px; font-size: 9px; line-height: 11px; width: 170px; }
  .intro { left: 25px; width: 580px; top: 560px; font-size: 12px; line-height: 15px; color: var(--muted); font-weight: 300; }

  .pricing { left: 0; top: 621px; width: 627px; height: 144px; background: var(--ink); color: var(--paper); }
  .pricing-title { top: 6px; color: var(--paper); }
  .plan { top: 43px; width: 180px; }
  .plan-price { font-size: 17px; line-height: 21px; font-weight: 400; }
  .plan-name { font-size: 17px; font-weight: 300; margin-top: 8px; }
  .plan-note { font-size: 11px; font-weight: 300; margin-top: 6px; }

  .contact-title { top: 774px; }
  .contact-label { font-size: 16px; line-height: 22px; font-weight: 300; width: 200px; }
  .reach-note { left: 213px; width: 200px; top: 832px; font-size: 8px; }
  .signup { left: 256px; top: 848px; width: 122px; height: 16px; display: flex; border: 1px solid var(--ink); }
  .signup-field { flex: 1; background: var(--paper); font-size: 6px; color: #888; padding: 4px 3px; }
  .signup-go { width: 15px; background: var(--ink); color: var(--paper); font-size: 6px; font-weight: 500; text-align: center; padding-top: 4px; }

  .site-footer { left: 0; top: 932px; width: 627px; height: 68px; background: var(--ink); }
  .social { left: 0; width: 627px; top: 22px; display: flex; justify-content: center; gap: 26px; }
  .social-dot { width: 24px; height: 24px; border-radius: 50%; background: var(--paper); }
</style>
</head>
<body>
<div class="page">
  <header class="site-header abs">
    <svg class="menu-icon abs" width="14" height="12" viewBox="0 0 14 12" aria-hidden="true">
      <rect y="0" width="14" height="2.4" fill="#fff"/><rect y="4.8" width="14" height="2.4" fill="#fff"/><rect y="9.6" width="14" height="2.4" fill="#fff"/>
    </svg>
    <div class="brand abs">Marrowind Fireworks &amp; Pyrotechnics</div>
  </header>

  <section class="hero abs" role="img" aria-label="Photograph of fireworks over the harbour bridge and opera house at night">
    <h1 class="hero-title abs center">Your Event Should Be Special</h1>
    <p class="hero-sub abs center">Let Us Help You Make Your<br>Events Unforgetable</p>
  </section>

  <h2 class="section-title services-title abs center">what we do</h2>
  <div class="service-photo photo-craft abs" role="img" aria-label="Photograph of pyrotechnic shells being prepared"></div>
  <div class="service-photo photo-stage abs" role="img" aria-label="Photograph of stage pyrotechnics at a concert"></div>
  <div class="service-photo photo-burst abs" role="img" aria-label="Photograph of a golden firework burst"></div>
  <p class="service-caption abs center" style="left:27px">Click here to see how Pyrotechnics work!</p>
  <p class="service-caption abs center" style="left:229px">Make your show unforgetable with timed pyrotechnics?</p>
  <p class="service-caption abs center" style="left:430px">Endles variations and durration avalible?</p>
  <p class="intro abs center">We need a web design and logo for a fireworks business in Sydney Australia, we do public display, weddings, tv, theatrical, clubs and any other organisation that wants to do something special.<br>More Info About Company, More Pictures</p>

  <section class="pricing abs">
    <h2 class="section-title pricing-title abs center">pricing</h2>
    <div class="plan abs center" style="left:22px">
      <div class="plan-price">$xxx.xx<br>per hour</div>
      <div class="plan-name">Pricing Quote 1</div>
      <div class="plan-note">with details</div>
    </div>
    <div class="plan abs center" style="left:224px">
      <div class="plan-price">$xxx.xx<br>per hour</div>
      <div class="plan-name">Pricing Quote 2</div>
      <div class="plan-note">with details</div>
    </div>
    <div class="plan abs center" style="left:425px">
      <div class="plan-price">$xxx.xx<br>per hour</div>
      <div class="plan-name">Pricing Quote 3</div>
      <div class="plan-note">with details</div>
    </div>
  </section>

  <h2 class="section-title contact-title abs center">get in touch</h2>
  <svg class="abs" style="left:75px;top:790px" width="74" height="74" viewBox="0 0 24 24" aria-label="phone">
    <path fill="#000" d="M6.6 2.2c.6-.4 1.4-.3 1.8.3l2.2 3.2c.4.6.3 1.3-.2 1.8L9 8.9c.9 2.3 2.9 4.5 5.4 5.9l1.5-1.3c.5-.4 1.3-.5 1.8-.1l3.1 2.3c.6.4.7 1.2.3 1.8l-1.3 2c-.7 1-2 1.5-3.2 1.1C10.3 18.6 5.6 13.7 3.8 7.4c-.3-1.2.1-2.4 1.1-3.1z"/>
  </svg>
  <p class="contact-label abs center" style="left:12px;top:877px">phone<br>(000) 000-0000</p>
  <p class="reach-note abs center">or we'll reach out to you</p>
  <div class="signup abs">
    <div class="signup-field">Enter Email Address</div>
    <div class="signup-go">GO</div>
  </div>
  <svg class="abs" style="left:478px;top:790px" width="74" height="74" viewBox="0 0 74 74" aria-label="email">
    <circle cx="37" cy="37" r="34" fill="none" stroke="#000" stroke-width="5"/>
    <text x="37" y="50" text-anchor="middle" font-family="Roboto, Arial, sans-serif" font-size="40" font-weight="500">@</text>
  </svg>
  <p class="contact-label abs center" style="left:415px;top:882px">email<br>hello@marrowindfx.com</p>

  <footer class="site-footer abs">
    <div class="social abs">
      <span class="social-dot" aria-label="social link"></span>
      <span class="social-dot" aria-label="social link"></span>
      <span class="social-dot" aria-label="social link"></span>
      <span class="social-dot" aria-label="social link"></span>
    </div>
  </footer>
</div>
</body>
</html>
```